Veltrano.co - Polar Expeditions Specialists

We need a modern, visually striking business card for Veltrano.co, a company specialized in selling expedition cruises to the most remote regions on Earth, with a focus on the Arctic and Antarctica. The design should instantly communicate that the cardholder is an expert in polar travel. Use clean, premium aesthetics with cool tones like icy blue and white, possibly incorporating polar imagery (ice, glaciers, penguins, etc.)

Attached the logo

Contact Information for Business Card

Feels high-end and trustworthy.. Visually memorable — encourages people to keep it

Colors
0054AA
0677BA
7BADD7
CADEEF
E8F1F8

Requirements
Must have
• ice, glaciers, penguins, montains
Nice to have
• modern, transparente,

```html
<!DOCTYPE html>
<html lang="en">
<head>
<meta charset="utf-8">
<title>Veltrano.co – Business Card</title>
<link rel="stylesheet" href="https://fonts.googleapis.com/css2?family=Poppins:wght@300;400;600;700&display=swap">
<style>
  :root {
    --stage: #646464;
    --paper: #ffffff;
    --brand-blue: #2f76bb;
    --deep-blue: #0054aa;
    --sky-blue: #7badd7;
    --ice-pale: #cadeef;
    --ice-mist: #e8f1f8;
    --ink: #0a0a0a;
    --ink-soft: #555b61;
    --water: #5f7a91;
    --glacier: #b9d0e4;
  }
  * { margin: 0; padding: 0; box-sizing: border-box; }
  html, body {
    width: 1200px; height: 1000px; overflow: hidden;
    background: var(--stage);
    font-family: "Poppins", sans-serif;
  }
  .canvas { position: relative; width: 1200px; height: 1000px; }

  .card {
    position: absolute;
    width: 694px; height: 398px;
    border-radius: 22px;
    overflow: hidden;
    box-shadow: 14px 16px 24px rgba(0,0,0,0.28);
  }

  /* ---------- Front ---------- */
  .card--front { left: 253px; top: 46px; background: var(--paper); }

  .front__photo {
    position: absolute; left: 0; top: 190px;
    width: 480px; height: 208px;
    background:
      linear-gradient(90deg, rgba(255,255,255,0) 0%, rgba(255,255,255,0) 55%, #fff 100%),
      linear-gradient(180deg, #fff 0%, #dbe7f1 18%, var(--glacier) 40%, #93b2cc 68%, #7d94a8 82%, var(--water) 100%);
  }
  .front__mark-faint {
    position: absolute; left: 50px; top: 60px;
    width: 260px; height: 260px;
    border-radius: 50%;
    background: rgba(180,196,228,0.55);
  }

  .front__info {
    position: absolute; right: 62px; top: 56px;
    text-align: right;
  }
  .brand-lockup {
    display: flex; justify-content: flex-end; align-items: center; gap: 8px;
  }
  .brand-mark {
    width: 46px; height: 46px; border-radius: 50%;
    background: var(--brand-blue); flex: none;
  }
  .brand-text { text-align: center; }
  .brand-name {
    color: var(--brand-blue);
    font-weight: 700;
    line-height: 1;
  }
  .front__info .brand-name { font-size: 33px; }
  .brand-tagline {
    color: var(--brand-blue);
    font-weight: 600;
  }
  .front__info .brand-tagline { font-size: 10px; margin-top: 4px; }

  .holder-name {
    margin-top: 58px;
    font-size: 28px; font-weight: 700;
    color: var(--ink); line-height: 1.1;
  }
  .holder-position {
    margin-top: 6px;
    font-size: 17px; font-weight: 400;
    letter-spacing: 3px; margin-right: -3px;
    color: var(--brand-blue);
  }

  .contact-list { list-style: none; margin-top: 30px; }
  .contact-list li {
    display: flex; justify-content: flex-end; align-items: center;
    gap: 18px;
    font-size: 23px; font-weight: 300;
    color: var(--ink-soft); line-height: 26px;
  }
  .contact-list svg { width: 18px; height: 18px; flex: none; }

  /* ---------- Back ---------- */
  .card--back {
    left: 248px; top: 511px;
  }
  .back__photo {
    position: absolute; inset: 0;
    background:
      radial-gradient(ellipse 250px 230px at 50% 48%, rgba(255,255,255,0.95) 0%, rgba(255,255,255,0.55) 50%, rgba(255,255,255,0) 100%),
      linear-gradient(180deg, #9fb0bf 0%, #c5d0da 28%, #dfe7ee 42%, #cfdde9 54%, var(--glacier) 64%, #9ab3c8 78%, #7890a5 90%, var(--water) 100%);
  }
  .back__mark {
    position: absolute; left: 300px; top: 100px;
    width: 94px; height: 94px; border-radius: 50%;
    background: var(--brand-blue);
  }
  .back__center {
    position: absolute; left: 0; right: 0; top: 228px;
    text-align: center;
  }
  .card--back .brand-name { font-size: 60px; }
  .card--back .brand-tagline { font-size: 19px; margin-top: 6px; }
</style>
</head>
<body>
<main class="canvas">

  <section class="card card--front">
    <div class="front__photo" role="img" aria-label="Photograph of a large iceberg floating on calm polar water, fading into white"></div>
    <div class="front__mark-faint" role="img" aria-label="Faint large brand mark decoration"></div>

    <div class="front__info">
      <div class="brand-lockup">
        <span class="brand-mark" role="img" aria-label="Brand mark"></span>
        <div class="brand-text">
          <div class="brand-name">Veltrano.co</div>
          <div class="brand-tagline">Polar Expeditions Specialists</div>
        </div>
      </div>

      <div class="holder-name">NAME SURNAME</div>
      <div class="holder-position">POSITION</div>

      <ul class="contact-list">
        <li>(123) 456-7890
          <svg viewBox="0 0 20 20" aria-hidden="true"><rect x="5" y="1" width="10" height="18" rx="2" fill="none" stroke="#2f76bb" stroke-width="2"/><circle cx="10" cy="16" r="1" fill="#2f76bb"/></svg>
        </li>
        <li>name@website.com
          <svg viewBox="0 0 20 20" aria-hidden="true"><rect x="1" y="4" width="18" height="12" fill="#2f76bb"/><path d="M1 4 L10 11 L19 4 M1 16 L8 10 M19 16 L12 10" fill="none" stroke="#fff" stroke-width="1.2"/></svg>
        </li>
        <li>website.com
          <svg viewBox="0 0 20 20" aria-hidden="true"><circle cx="10" cy="10" r="8" fill="#2f76bb"/><g fill="none" stroke="#fff" stroke-width="0.9"><ellipse cx="10" cy="10" rx="3.5" ry="8"/><line x1="2" y1="10" x2="18" y2="10"/><line x1="3" y1="6" x2="17" y2="6"/><line x1="3" y1="14" x2="17" y2="14"/><line x1="10" y1="2" x2="10" y2="18"/></g></svg>
        </li>
      </ul>
    </div>
  </section>

  <section class="card card--back">
    <div class="back__photo" role="img" aria-label="Photograph of glaciers and icebergs over still polar water with a soft light glow"></div>
    <div class="back__mark" role="img" aria-label="Brand mark"></div>
    <div class="back__center">
      <div class="brand-name">Veltrano.co</div>
      <div class="brand-tagline">Polar Expeditions Specialists</div>
    </div>
  </section>

</main>
</body>
</html>
```